Movie poster for short film: TINFOIL

We need a creative, artistic, stylized poster design for our short film TINFOIL. We would like to see designs with graphics and bold colors more than photographs. The photographs we are posting are more for reference- you do not have to use them in the poster! We are looking for something clean and simple. The film is a drama so please don't make it funny. The mood of the film is thoughtful and introspective. Name of film should be in all caps. Things to include in the poster:
Name of film: TINFOIL
Paper Lantern Productions
Starring Marta Kowelski

Here is a brief plot synopsis: TINFOIL follows one night in the life of a rebellious young woman who breaks into a diner after hours with a can of spray paint. Her intentions change after she ends up discovering what's left of a love story.

The movie is somewhat experimental, set to music for part of it with no dialog. The whole movie takes place in an old fashioned diner.

Target Market(s)

Film festival attendees between the ages of 20-50

Industry/Entity Type

Movie

Font styles to use
Sans Serif

Requirements
Must have
• See project description above- also the film is somewhat dark in nature so please don't make it too 'happy' looking.

```html
<!DOCTYPE html>
<html lang="en">
<head>
<meta charset="utf-8">
<title>TINFOIL — Poster</title>
<link rel="stylesheet" href="https://fonts.googleapis.com/css2?family=Jost:wght@400;700&display=swap">
<style>
  :root {
    --page: #ffffff;
    --ink: #0b0b0c;
    --midnight: #1c2533;
    --dusk: #2e4256;
    --harbor: #35596a;
    --steel: #4f6375;
    --slate: #6c7885;
    --pewter: #8d959d;
    --ember: #6e4347;
    --silver: #b5bbc1;
    --haze: #cfd4d9;
    --fog: #e2e4e7;
    --edge: #e4e4e4;
  }
  * { box-sizing: border-box; margin: 0; padding: 0; }
  html, body {
    width: 1200px; height: 1000px; overflow: hidden;
    background: var(--page);
    font-family: "Jost", "Century Gothic", sans-serif;
  }
  .poster {
    position: absolute; left: 286px; top: 18px;
    width: 640px; height: 960px;
    background: var(--page);
    outline: 1px solid var(--edge);
  }
  .dot-grid {
    position: absolute; left: 12px; top: 0;
    display: grid;
    grid-template-columns: repeat(7, 88px);
    grid-template-rows: repeat(11, 87.6px);
    font-weight: 700;
  }
  .cell { display: flex; align-items: center; justify-content: center; }
  .dot { width: 47px; height: 47px; border-radius: 50%; }
  .dot.midnight { background: var(--midnight); }
  .dot.dusk { background: var(--dusk); }
  .dot.harbor { background: var(--harbor); }
  .dot.steel { background: var(--steel); }
  .dot.slate { background: var(--slate); }
  .dot.pewter { background: var(--pewter); }
  .dot.ember { background: var(--ember); }
  .dot.silver { background: var(--silver); }
  .dot.haze { background: var(--haze); }
  .dot.fog { background: var(--fog); }
  .title-letter {
    font-weight: 700; font-size: 60px; line-height: 1;
    color: var(--ink);
  }
  .credit {
    position: absolute; left: 0; width: 640px; top: 792px;
    text-align: center;
    font-size: 17px; font-weight: 400; letter-spacing: 0.3px; line-height: 1;
    color: var(--ink);
  }
  .studio {
    width: 90px; height: 90px; background: var(--ink);
    transform: translateY(-12px);
    display: flex; align-items: flex-end; justify-content: center;
    padding: 0 6px 12px;
  }
  .studio-name {
    color: var(--page); font-size: 7px; font-weight: 400;
    text-align: center; line-height: 1.3; letter-spacing: 0.4px;
    text-transform: uppercase;
  }
</style>
</head>
<body>
<main class="poster">
  <h1 class="dot-grid" aria-label="TINFOIL">
    <span class="cell"><span class="dot dusk"></span></span>
    <span class="cell"><span class="dot midnight"></span></span>
    <span class="cell"><span class="dot steel"></span></span>
    <span class="cell"><span class="dot midnight"></span></span>
    <span class="cell"><span class="dot harbor"></span></span>
    <span class="cell"><span class="dot dusk"></span></span>
    <span class="cell"><span class="dot midnight"></span></span>

    <span class="cell"><span class="title-letter">T</span></span>
    <span class="cell"><span class="dot harbor"></span></span>
    <span class="cell"><span class="title-letter">I</span></span>
    <span class="cell"><span class="dot dusk"></span></span>
    <span class="cell"><span class="dot slate"></span></span>
    <span class="cell"><span class="dot midnight"></span></span>
    <span class="cell"><span class="dot steel"></span></span>

    <span class="cell"><span class="dot midnight"></span></span>
    <span class="cell"><span class="dot steel"></span></span>
    <span class="cell"><span class="dot ember"></span></span>
    <span class="cell"><span class="dot harbor"></span></span>
    <span class="cell"><span class="title-letter">N</span></span>
    <span class="cell"><span class="dot dusk"></span></span>
    <span class="cell"><span class="dot slate"></span></span>

    <span class="cell"><span class="title-letter">F</span></span>
    <span class="cell"><span class="dot dusk"></span></span>
    <span class="cell"><span class="dot slate"></span></span>
    <span class="cell"><span class="dot midnight"></span></span>
    <span class="cell"><span class="dot steel"></span></span>
    <span class="cell"><span class="dot harbor"></span></span>
    <span class="cell"><span class="dot dusk"></span></span>

    <span class="cell"><span class="dot slate"></span></span>
    <span class="cell"><span class="title-letter">O</span></span>
    <span class="cell"><span class="dot steel"></span></span>
    <span class="cell"><span class="dot pewter"></span></span>
    <span class="cell"><span class="dot dusk"></span></span>
    <span class="cell"><span class="dot slate"></span></span>
    <span class="cell"><span class="dot harbor"></span></span>

    <span class="cell"><span class="dot pewter"></span></span>
    <span class="cell"><span class="dot harbor"></span></span>
    <span class="cell"><span class="dot slate"></span></span>
    <span class="cell"><span class="dot steel"></span></span>
    <span class="cell"><span class="dot pewter"></span></span>
    <span class="cell"><span class="title-letter">I</span></span>
    <span class="cell"><span class="dot steel"></span></span>

    <span class="cell"><span class="dot steel"></span></span>
    <span class="cell"><span class="dot pewter"></span></span>
    <span class="cell"><span class="dot silver"></span></span>
    <span class="cell"><span class="dot slate"></span></span>
    <span class="cell"><span class="dot pewter"></span></span>
    <span class="cell"><span class="dot silver"></span></span>
    <span class="cell"><span class="title-letter">L</span></span>

    <span class="cell"><span class="dot silver"></span></span>
    <span class="cell"><span class="dot slate"></span></span>
    <span class="cell"><span class="dot haze"></span></span>
    <span class="cell"><span class="dot pewter"></span></span>
    <span class="cell"><span class="dot silver"></span></span>
    <span class="cell"><span class="dot pewter"></span></span>
    <span class="cell"><span class="dot haze"></span></span>

    <span class="cell"><span class="dot haze"></span></span>
    <span class="cell"><span class="dot silver"></span></span>
    <span class="cell"><span class="dot pewter"></span></span>
    <span class="cell"><span class="dot haze"></span></span>
    <span class="cell"><span class="dot silver"></span></span>
    <span class="cell"><span class="dot fog"></span></span>
    <span class="cell"><span class="dot silver"></span></span>

    <span class="cell"><span class="dot fog"></span></span>
    <span class="cell"><span class="dot haze"></span></span>
    <span class="cell"><span class="dot fog"></span></span>
    <span class="cell"><span class="dot silver"></span></span>
    <span class="cell"><span class="dot fog"></span></span>
    <span class="cell"><span class="dot haze"></span></span>
    <span class="cell"><span class="dot fog"></span></span>

    <span class="cell"><span class="dot haze"></span></span>
    <span class="cell"><span class="dot fog"></span></span>
    <span class="cell"><span class="dot haze"></span></span>
    <span class="cell"><span class="studio"><span class="studio-name">Paper Lantern Productions</span></span></span>
    <span class="cell"><span class="dot fog"></span></span>
    <span class="cell"><span class="dot haze"></span></span>
    <span class="cell"><span class="dot fog"></span></span>
  </h1>
  <p class="credit">STARRING MARTA KOWELSKI</p>
</main>
</body>
</html>
```